High-end construction company needs a business card design

We need a modern looking business card that draws people in, is memorable and looks so good people will want to sick it on their fridges.
On the first side what is needed are:
Logo
My name - Tomasz Brelwik
Title - Managing Director
Website - www.varkelt.co.uk
Email - tomasz@varkelt.co.uk
Telephone - 020 5194 6281
Mobile - 07845139072
On the back side was is needed is a list of all the services we provide:
-Kitchen Renovations
-Bathroom Renovations
-House Renovations
-Garage Conversions
-Extensions
-Loft Conversions
-Conservatories
-Carpentry
-Tiling
-Electrical
-Plumbing & Heating
-Bricklaying
-Landscaping
-Decorating
-Plastering
We would like the colours to be the same shades as on the logo with grey or black for the words.
Target Market(s)
Anyone who needs building work done
Contact Information for Business Card
This business card is for a construction company which strives to deliver excellent service and quality.
The look and feel of the card should represent this.
Requirements
Must have
- On the first side what is needed are:
Logo
My name - Tomasz Brelwik
Title - Managing Director
Website - www.varkelt.co.uk
Email - tomasz@varkelt.co.uk
Telephone - 020 5194 6281
Mobile - 07845139072
Nice to have
- Cool looking features

```html
<!DOCTYPE html>
<html lang="en">
<head>
<meta charset="utf-8">
<title>Varkelt Construction Ltd — Business Card</title>
<link href="https://fonts.googleapis.com/css2?family=Open+Sans:wght@400;600;700&display=swap" rel="stylesheet">
<style>
  :root {
    --stage: #e4e4e4;
    --green: #6db842;
    --green-dark: #4b8b3b;
    --green-text: #4f9a3a;
    --ink: #2b2b2b;
    --card-white: #f4f4f4;
    --white: #ffffff;
  }
  * { box-sizing: border-box; margin: 0; padding: 0; }
  html, body { width: 1200px; height: 960px; overflow: hidden; }
  body {
    background: var(--stage);
    font-family: "Open Sans", Arial, sans-serif;
    position: relative;
  }
  .card {
    position: absolute;
    left: 330px;
    width: 551px;
    height: 357px;
    overflow: hidden;
  }
  /* Services side */
  .card--services { top: 105px; background: var(--green); }
  .service-list {
    position: absolute;
    left: 36px;
    top: 24px;
    list-style: none;
  }
  .service-list li {
    font-size: 14.5px;
    line-height: 20.6px;
    color: var(--ink);
    text-transform: uppercase;
    padding-left: 12px;
    position: relative;
  }
  .service-list li::before {
    content: "";
    position: absolute;
    left: 0;
    top: 8px;
    width: 6px;
    height: 6px;
    border-radius: 50%;
    background: var(--ink);
  }
  .hero-art {
    position: absolute;
    left: 125px;
    top: 90px;
    width: 405px;
    height: 267px;
    background: linear-gradient(135deg, rgba(255,255,255,0.15) 0%, rgba(255,255,255,0.85) 55%, var(--green-dark) 100%);
    clip-path: polygon(0 100%, 100% 0, 100% 80%, 35% 80%, 35% 100%);
  }
  .web-band {
    position: absolute;
    left: 220px;
    top: 298px;
    width: 331px;
    height: 25px;
    background: var(--green-dark);
    color: var(--white);
    font-size: 14px;
    letter-spacing: 1px;
    line-height: 25px;
    text-align: right;
    padding-right: 40px;
  }
  /* Contact side */
  .card--contact { top: 504px; background: var(--card-white); }
  .brand-name {
    position: absolute;
    left: 50px;
    top: 172px;
    width: 215px;
    color: var(--green);
    font-weight: 700;
    text-align: center;
    line-height: 1;
  }
  .brand-name .brand-word { display: block; font-size: 44px; letter-spacing: 1px; }
  .brand-name .brand-sub { display: block; font-size: 13.5px; letter-spacing: 1.6px; margin-top: 6px; }
  .divider {
    position: absolute;
    left: 301px;
    width: 2px;
    background: var(--green);
  }
  .divider--top { top: 108px; height: 40px; }
  .divider--bottom { top: 158px; height: 90px; }
  .person {
    position: absolute;
    left: 340px;
    top: 112px;
  }
  .person-name { font-size: 18px; font-weight: 700; color: var(--green-text); line-height: 22px; }
  .person-title { font-size: 14px; color: var(--ink); line-height: 20px; }
  .contact-list {
    position: absolute;
    left: 340px;
    top: 168px;
    list-style: none;
  }
  .contact-list li {
    display: flex;
    align-items: center;
    font-size: 14px;
    line-height: 19.5px;
    color: var(--ink);
  }
  .contact-list svg { width: 12px; height: 12px; margin-right: 6px; fill: var(--green-dark); flex: none; }
</style>
</head>
<body>
  <section class="card card--services">
    <ul class="service-list">
      <li>Kitchen Renovations</li>
      <li>Bathroom Renovations</li>
      <li>House Renovations</li>
      <li>Garage Conversions</li>
      <li>Extensions</li>
      <li>Loft Conversions</li>
      <li>Conservatories</li>
      <li>Carpentry</li>
      <li>Electrical</li>
      <li>Plumbing &amp; Heating</li>
      <li>Bricklaying</li>
      <li>Landscaping</li>
      <li>Decorating</li>
      <li>Plastering</li>
      <li>Tiling</li>
    </ul>
    <div class="hero-art" role="img" aria-label="Illustration of an excavator arm reaching over a house roof and city buildings"></div>
    <div class="web-band">www.varkelt.co.uk</div>
  </section>

  <section class="card card--contact">
    <div class="brand-name">
      <span class="brand-word">VARKELT</span>
      <span class="brand-sub">CONSTRUCTION LTD</span>
    </div>
    <span class="divider divider--top"></span>
    <span class="divider divider--bottom"></span>
    <div class="person">
      <p class="person-name">Tomasz Brelwik</p>
      <p class="person-title">Managing Director</p>
    </div>
    <ul class="contact-list">
      <li><svg viewBox="0 0 24 24"><path d="M6.6 10.8a15.1 15.1 0 0 0 6.6 6.6l2.2-2.2c.3-.3.7-.4 1-.2 1.1.4 2.3.6 3.6.6.6 0 1 .4 1 1V20c0 .6-.4 1-1 1A17 17 0 0 1 3 4c0-.6.4-1 1-1h3.5c.6 0 1 .4 1 1 0 1.3.2 2.5.6 3.6.1.3 0 .7-.2 1z"/></svg>020 5194 6281</li>
      <li><svg viewBox="0 0 24 24"><path d="M7 1h10a2 2 0 0 1 2 2v18a2 2 0 0 1-2 2H7a2 2 0 0 1-2-2V3a2 2 0 0 1 2-2zm0 3v14h10V4zm5 15.5a1 1 0 1 0 0 2 1 1 0 0 0 0-2z"/></svg>07845139072</li>
      <li><svg viewBox="0 0 24 24"><path d="M2 5h20v14H2zm2 2v.5l8 5.5 8-5.5V7zm0 3v7h16v-7l-8 5.5z"/></svg>tomasz@varkelt.co.uk</li>
      <li><svg viewBox="0 0 24 24"><path d="M12 2a10 10 0 1 0 0 20 10 10 0 0 0 0-20zm6.9 6h-3a15 15 0 0 0-1.3-3.9A8 8 0 0 1 18.9 8zM12 4c.8 1.2 1.5 2.5 1.9 4h-3.8c.4-1.5 1.1-2.8 1.9-4zM4.3 14a8 8 0 0 1 0-4h3.4a16 16 0 0 0 0 4zm.8 2h3a15 15 0 0 0 1.3 3.9A8 8 0 0 1 5.1 16zm3-8h-3a8 8 0 0 1 4.3-3.9C8.8 5.3 8.4 6.6 8.1 8zM12 20c-.8-1.2-1.5-2.5-1.9-4h3.8c-.4 1.5-1.1 2.8-1.9 4zm2.3-6H9.7a14 14 0 0 1 0-4h4.6a14 14 0 0 1 0 4zm.3 5.9c.6-1.2 1-2.5 1.3-3.9h3a8 8 0 0 1-4.3 3.9zm1.7-5.9a16 16 0 0 0 0-4h3.4a8 8 0 0 1 0 4z"/></svg>www.varkelt.co.uk</li>
    </ul>
  </section>
</body>
</html>
```